New, modern business card for growing audiology practice

We need a new business card for our audiology practice. Our logo and website have recently changed (more modern) and we want our business cards to reflect this change.
We conduct hearing tests, perform earwax removals, and fit & dispense hearing aids to our patients. We are a family owned practice in which the owner is the one who works directly with the patient. I have attached logos in various formats to use, as well as two ideas I found on this website; as well as a scanned copy of our current logo. Good luck!

Industry/Entity Type

Business

Contact Information for Business Card

Company name: Tolvera Hearing Center
Provider name: Peter Wolstenby, Au.D. F/NSB
Phone number: (440) 683-5127
Address: 837 W. Lindell Ave. Brenwick Falls, OH 44097
email: tolverahearing@postvane.com
website: tolverahearing.com

Colors
000000
aaaaaa
dbdbdb
cacaca
9bcb3c
afd23c
cadf82
b1b1b1

Requirements
Must have
• My card must include information in the "details" section. In the attached images, I found a few that I liked and I would like to model after - "brisky bouncin'" and "Sound Method Center".
• Must be horizontal.
• Must include logos provided. I uploaded them in various file formats and various ways.
• Must match logo font, if possible, if not, please get as close as you can.
Nice to have
• I really like the idea of having a color on one side with just the logo and company name and the contact information and provider name on the other side. I also really like the idea of having the main color dominating on the logo/company side with accent of that same color on the contact side of the card.
Should not have
• Must not be vertical.

```html
<!DOCTYPE html>
<html lang="en">
<head>
<meta charset="utf-8">
<title>Tolvera Hearing Center – Business Card</title>
<link rel="stylesheet" href="https://fonts.googleapis.com/css2?family=Roboto:wght@400;500&family=Roboto+Condensed:wght@700&display=swap">
<style>
  :root {
    --backdrop: #d4aa82;
    --card-dark: #18191b;
    --card-light: #f1f1f1;
    --brand-green: #7aa442;
    --ink: #1e1e1e;
    --white: #ffffff;
    --url-grey: #dcdcdc;
  }
  * { margin: 0; padding: 0; box-sizing: border-box; }
  html, body { width: 1200px; height: 960px; overflow: hidden; }
  body {
    background: var(--backdrop);
    font-family: "Roboto", Arial, sans-serif;
    position: relative;
  }
  .card {
    position: absolute;
    left: 320px;
    width: 600px;
    height: 342px;
    border-radius: 18px;
    overflow: hidden;
  }
  .card--front { top: 108px; background: var(--card-dark); }
  .card--back { top: 493px; background: var(--card-light); }

  .wordmark {
    position: absolute;
    display: flex;
    align-items: center;
    font-family: "Roboto", Arial, sans-serif;
    font-weight: 400;
    text-transform: uppercase;
    white-space: nowrap;
  }
  .wordmark__dot { border-radius: 50%; background: var(--brand-green); flex: none; }
  .card--front .wordmark {
    left: 92px; top: 153px;
    font-size: 29.5px; color: var(--white); letter-spacing: 0.2px;
  }
  .card--front .wordmark__dot { width: 24px; height: 24px; margin-right: 16px; }
  .front-url {
    position: absolute; left: 0; right: 0; top: 286px;
    text-align: center; font-size: 14.5px; letter-spacing: 4.2px;
    color: var(--url-grey);
  }

  .green-panel { position: absolute; left: 0; top: 0; width: 340px; height: 342px; }
  .provider { position: absolute; left: 29px; top: 25px; color: var(--white); }
  .provider__name {
    font-family: "Roboto Condensed", "Arial Narrow", sans-serif;
    font-weight: 700; font-size: 21px; text-transform: uppercase;
  }
  .provider__title { font-size: 14px; font-weight: 500; margin-top: 2px; letter-spacing: 0.3px; }
  .contact { position: absolute; left: 29px; top: 212px; color: var(--white); font-size: 14px; line-height: 18px; }
  .contact__address { margin-bottom: 10px; }
  .contact__row { display: flex; align-items: center; gap: 6px; height: 19.5px; }
  .contact__row svg { width: 13px; height: 13px; flex: none; fill: var(--white); }
  .card--back .wordmark {
    left: 305px; top: 283px;
    font-size: 18.5px; color: var(--ink);
  }
  .card--back .wordmark__dot { width: 14px; height: 14px; margin-right: 12px; }
</style>
</head>
<body>

<section class="card card--front" aria-label="Card front">
  <div class="wordmark"><span class="wordmark__dot"></span>Tolvera Hearing Center</div>
  <p class="front-url">www.tolverahearing.com</p>
</section>

<section class="card card--back" aria-label="Card back">
  <svg class="green-panel" viewBox="0 0 340 342" aria-hidden="true">
    <path fill="var(--brand-green)" d="M0 0 H240 C310 0 345 60 338 120 C332 180 290 200 280 245 C272 290 265 332 225 342 H0 Z"/>
  </svg>

  <div class="provider">
    <p class="provider__name">Peter Wolstenby</p>
    <p class="provider__title">AU.D. F/NSB</p>
  </div>

  <div class="contact">
    <p class="contact__address">837 W. Lindell Ave.<br>Brenwick Falls, OH 44097</p>
    <p class="contact__row">
      <svg viewBox="0 0 24 24"><path d="M6.6 10.8a15.1 15.1 0 0 0 6.6 6.6l2.2-2.2c.3-.3.7-.4 1-.2 1.1.4 2.3.6 3.6.6.6 0 1 .4 1 1V20c0 .6-.4 1-1 1A17 17 0 0 1 3 4c0-.6.4-1 1-1h3.5c.6 0 1 .4 1 1 0 1.3.2 2.5.6 3.6.1.3 0 .7-.2 1z"/></svg>
      (440) 683-5127
    </p>
    <p class="contact__row">
      <svg viewBox="0 0 24 24"><path d="M2 5h20v14H2z M2 5l10 8 10-8" stroke="var(--brand-green)" stroke-width="1.6"/></svg>
      tolverahearing@postvane.com
    </p>
    <p class="contact__row">
      <svg viewBox="0 0 24 24"><path d="M12 2a10 10 0 1 0 0 20 10 10 0 0 0 0-20zm-1 17.9A8 8 0 0 1 4.2 10L9 15v1a2 2 0 0 0 2 2zm6.9-2.5A2 2 0 0 0 16 16h-1v-3a1 1 0 0 0-1-1H8v-2h2a1 1 0 0 0 1-1V7h2a2 2 0 0 0 2-2v-.4a8 8 0 0 1 2.9 12.8z"/></svg>
      tolverahearing.com
    </p>
  </div>

  <div class="wordmark"><span class="wordmark__dot"></span>Tolvera Hearing Center</div>
</section>

</body>
</html>
```